Business Card Design

Business sales of reconditioned / used batteries with mobile delivery and install services. Customers base majority are auto car sales lots and individuals.

Card need to convey quality product reliability and quick prompt professional service.

Card must reflect excellence in customer care and product being offered

Target Market(s)

Auto car lots new and used. Auto repair shops. Individuals.

Industry/Entity Type

Business

Contact Information for Business Card

Batteries Q-Swift
Cars, Trucks, Boats, Motorcycles, lawn mowers, power tools
Delivery & install available most vehicles
Mon-Sat 9-6pm
Dale Morrick 501-738-2054
*product warranty 6 month shelf life battery/1 year blems battery

```html
<!DOCTYPE html>
<html lang="en">
<head>
<meta charset="utf-8">
<title>Batteries Q-Swift – Business Card</title>
<link rel="stylesheet" href="https://fonts.googleapis.com/css2?family=Open+Sans:wght@400;700&display=swap">
<style>
  :root {
    --page: #ffffff;
    --card: #ffffff;
    --band-grey: #e8e8e8;
    --ink: #111111;
    --panel: #000000;
    --red: #e30613;
    --white: #ffffff;
  }
  * { margin: 0; padding: 0; box-sizing: border-box; }
  html, body {
    width: 1200px; height: 1000px; overflow: hidden;
    background: var(--page);
    font-family: "Open Sans", Arial, sans-serif;
  }
  .card {
    position: absolute; left: 60px; top: 183px;
    width: 1086px; height: 637px;
    background: var(--card);
    box-shadow: 4px 6px 10px rgba(0,0,0,0.35);
    overflow: hidden;
  }
  .card-art { position: absolute; inset: 0; }
  .brand {
    position: absolute; left: 48px; top: 86px;
    display: flex; align-items: center; gap: 14px;
    font-weight: 700; font-size: 48px; line-height: 1;
    color: var(--ink); letter-spacing: 0.5px;
  }
  .brand-mark { width: 26px; height: 26px; background: var(--red); }
  .services {
    position: absolute; left: 50px; top: 175px;
    list-style: none;
  }
  .services li {
    display: flex; align-items: center; gap: 10px;
    font-size: 33px; line-height: 42.5px; color: var(--ink);
  }
  .services svg { width: 30px; height: 26px; flex: none; }
  .warranty {
    position: absolute; left: 46px; top: 500px;
    font-size: 24px; line-height: 34px; color: var(--ink);
    text-indent: -20px; padding-left: 20px; width: 480px;
  }
  .contact {
    position: absolute; right: 38px; top: 262px;
    text-align: right; color: var(--white);
  }
  .contact-name { color: var(--red); font-size: 44px; line-height: 54px; }
  .contact-phone { font-weight: 700; font-size: 58px; line-height: 66px; }
  .contact-hours { font-size: 33px; margin-top: 30px; }
</style>
</head>
<body>
<main class="card">
  <svg class="card-art" viewBox="0 0 1086 637" width="1086" height="637" aria-hidden="true">
    <defs>
      <linearGradient id="accent-band" x1="0" y1="0" x2="0" y2="1">
        <stop offset="0" stop-color="#f7b8a2"/>
        <stop offset="0.5" stop-color="#e30613"/>
        <stop offset="1" stop-color="#f7c2ae"/>
      </linearGradient>
    </defs>
    <g class="bg-bands" fill="var(--band-grey)">
      <polygon points="130,0 260,0 560,637 430,637"/>
      <polygon points="310,0 430,0 700,637 580,637"/>
      <polygon points="0,150 200,150 330,300 200,480 0,480"/>
    </g>
    <polygon class="accent-band" fill="url(#accent-band)" points="710,0 760,0 560,302 783,637 733,637 512,302"/>
    <polygon class="dark-panel" fill="var(--panel)" points="760,0 1086,0 1086,637 783,637 560,302"/>
  </svg>

  <div class="brand"><span class="brand-mark"></span>BATTERIES Q-SWIFT</div>

  <ul class="services">
    <li><svg viewBox="0 0 30 26"><path d="M0 0h9l9 13-9 13H0l9-13z M12 0h9l9 13-9 13h-9l9-13z" fill="var(--red)"/></svg>Trucks</li>
    <li><svg viewBox="0 0 30 26"><path d="M0 0h9l9 13-9 13H0l9-13z M12 0h9l9 13-9 13h-9l9-13z" fill="var(--red)"/></svg>Boats</li>
    <li><svg viewBox="0 0 30 26"><path d="M0 0h9l9 13-9 13H0l9-13z M12 0h9l9 13-9 13h-9l9-13z" fill="var(--red)"/></svg>Motorcycles</li>
    <li><svg viewBox="0 0 30 26"><path d="M0 0h9l9 13-9 13H0l9-13z M12 0h9l9 13-9 13h-9l9-13z" fill="var(--red)"/></svg>Lawn mowers</li>
    <li><svg viewBox="0 0 30 26"><path d="M0 0h9l9 13-9 13H0l9-13z M12 0h9l9 13-9 13h-9l9-13z" fill="var(--red)"/></svg>Power tools</li>
    <li><svg viewBox="0 0 30 26"><path d="M0 0h9l9 13-9 13H0l9-13z M12 0h9l9 13-9 13h-9l9-13z" fill="var(--red)"/></svg>Delivery &amp; Install available</li>
    <li><svg viewBox="0 0 30 26"><path d="M0 0h9l9 13-9 13H0l9-13z M12 0h9l9 13-9 13h-9l9-13z" fill="var(--red)"/></svg>Most vehicles</li>
  </ul>

  <p class="warranty">* product warranty 6 month shelf life battery / 1 year blems battery</p>

  <section class="contact">
    <p class="contact-name">DALE MORRICK</p>
    <p class="contact-phone">501 738 2054</p>
    <p class="contact-hours">Mon-Sat 9-6pm</p>
  </section>
</main>
</body>
</html>
```